BOLD PINE HEATING AND COOLING

Industry/Entity Type

Hvac

Requirements
Must have
• logo
My name: Gavin Pruszynski
Phone number 555-309-4461
Text:
Furnace and AC repairs
New furnace and AC installation
Ductwork
Gas lines
Water Tanks
Tankless water heaters
Nice to have
• Profesional modern look

```html
<!DOCTYPE html>
<html lang="en">
<head>
<meta charset="utf-8">
<title>Bold Pine Heating and Cooling – Business Card</title>
<link rel="stylesheet" href="https://fonts.googleapis.com/css2?family=Arimo:wght@400;700&display=swap">
<style>
  :root {
    --backdrop: #e4e5e8;
    --card: #ffffff;
    --brand-blue: #1f5fae;
    --band-blue: #1c5cb4;
    --accent-red: #d3222a;
    --ink-white: #ffffff;
  }
  * { box-sizing: border-box; margin: 0; padding: 0; }
  html, body {
    width: 1200px; height: 997px; overflow: hidden;
    background: var(--backdrop);
  }
  .canvas { position: relative; width: 1200px; height: 997px; }
  .card {
    position: absolute; left: 250px; width: 700px; height: 400px;
    background: var(--card);
    box-shadow: 0 6px 20px rgba(0,0,0,0.18);
    overflow: hidden;
  }
  .card--front { top: 62px; }
  .card--back { top: 535px; }

  /* Brand name: plain text with a single circle */
  .brand {
    position: absolute; display: flex; align-items: center;
    font-family: "Arimo", sans-serif; font-weight: 700; color: var(--brand-blue);
  }
  .brand__mark { flex: none; background: var(--brand-blue); border-radius: 50%; }
  .brand__name { line-height: 1.15; letter-spacing: 0.02em; }

  .card--front .brand { left: 0; right: 0; top: 150px; justify-content: center; gap: 24px; }
  .card--front .brand__mark { width: 90px; height: 90px; }
  .card--front .brand__name { font-size: 34px; width: 400px; }

  .card--back .brand { left: 110px; top: 52px; gap: 20px; }
  .card--back .brand__mark { width: 64px; height: 64px; }
  .card--back .brand__name { font-size: 26px; width: 320px; }

  /* Contact band */
  .contact-band {
    position: absolute; left: 0; right: 0; top: 160px; height: 74px;
    background: var(--band-blue); color: var(--ink-white);
    font-family: "Arimo", sans-serif;
    padding: 14px 0 0 250px;
  }
  .contact-band__name { font-weight: 700; font-size: 17px; letter-spacing: 0.04em; }
  .contact-band__phone {
    display: flex; align-items: center; gap: 7px;
    font-size: 15px; margin-top: 5px;
  }
  .contact-band__phone svg { width: 14px; height: 14px; fill: var(--ink-white); }

  /* Service lists */
  .services {
    position: absolute; list-style: none;
    font-family: "Arimo", sans-serif; font-size: 15px; color: var(--brand-blue);
    line-height: 1.45;
  }
  .services li { display: flex; align-items: center; gap: 9px; }
  .services li::after, .services li::before {
    width: 6px; height: 6px; border-radius: 50%; background: var(--accent-red);
  }
  .services--primary { right: 34px; top: 250px; text-align: right; }
  .services--primary li { justify-content: flex-end; }
  .services--primary li::after { content: ""; }
  .services--secondary { left: 40px; top: 300px; }
  .services--secondary li::before { content: ""; }
</style>
</head>
<body>
<main class="canvas">

  <section class="card card--front" aria-label="Card front">
    <div class="brand">
      <span class="brand__mark" aria-hidden="true"></span>
      <span class="brand__name">BOLD PINE HEATING AND COOLING</span>
    </div>
  </section>

  <section class="card card--back" aria-label="Card back">
    <div class="brand">
      <span class="brand__mark" aria-hidden="true"></span>
      <span class="brand__name">BOLD PINE HEATING AND COOLING</span>
    </div>

    <div class="contact-band">
      <p class="contact-band__name">GAVIN PRUSZYNSKI</p>
      <p class="contact-band__phone">
        <svg viewBox="0 0 24 24" aria-hidden="true"><path d="M6.6 10.8a15.1 15.1 0 0 0 6.6 6.6l2.2-2.2a1 1 0 0 1 1-.25 11.4 11.4 0 0 0 3.6.57 1 1 0 0 1 1 1V20a1 1 0 0 1-1 1A17 17 0 0 1 3 4a1 1 0 0 1 1-1h3.5a1 1 0 0 1 1 1c0 1.25.2 2.45.57 3.57a1 1 0 0 1-.25 1z"/></svg>
        555-309-4461
      </p>
    </div>

    <ul class="services services--primary">
      <li>Tankless water heaters</li>
      <li>Furnace and AC repairs</li>
      <li>New furnace and AC installation</li>
    </ul>

    <ul class="services services--secondary">
      <li>Gas lines</li>
      <li>Ductwork</li>
      <li>Water Tanks</li>
    </ul>
  </section>

</main>
</body>
</html>
```